Business Cards for a law firm

Business cards for our law firm. Use our silhoette logo and OAK PARTNERS - check our website (www.oakpartners.example)

Contact Information for Business Card

our silhouette logo, OAK PARTNERS, 800-555-0147, Dorian Pemberton, dorian@oakpartners.example

Requirements
Must have
• our silhouette logo, OAK PARTNERS, 800-555-0147, Dorian Pemberton, dorian@oakpartners.example

```html
<!DOCTYPE html>
<html lang="en">
<head>
<meta charset="utf-8">
<title>Oak Partners – Business Cards</title>
<link rel="stylesheet" href="https://fonts.googleapis.com/css2?family=Montserrat:wght@400;700&display=swap">
<style>
  :root {
    --page-bg: #e2e7e9;
    --card-navy: #233367;
    --ink-white: #ffffff;
    --figure-light: #3f9ad8;
    --figure-mid: #2a4589;
    --figure-deep: #222f66;
  }
  * { margin: 0; padding: 0; box-sizing: border-box; }
  html, body { width: 1200px; height: 960px; overflow: hidden; }
  body {
    background: var(--page-bg);
    font-family: "Montserrat", sans-serif;
    color: var(--ink-white);
    position: relative;
  }
  .card {
    position: absolute;
    left: 248px;
    width: 706px;
    height: 404px;
    background: var(--card-navy);
  }
  .card--front { top: 58px; }
  .card--back { top: 500px; }

  /* Front */
  .front-mark {
    position: absolute;
    left: 112px; top: 160px;
    width: 84px; height: 84px;
    border-radius: 50%;
    background: var(--ink-white);
  }
  .front-name {
    position: absolute;
    left: 226px; top: 140px;
    font-weight: 400;
    font-size: 56px;
    line-height: 50px;
    letter-spacing: 0.02em;
    white-space: nowrap;
  }

  /* Back */
  .back-brand {
    position: absolute;
    left: 29px; top: 44px;
    display: flex; align-items: center; gap: 12px;
  }
  .back-brand__mark {
    width: 30px; height: 30px;
    background: var(--ink-white);
  }
  .back-brand__name {
    font-weight: 400;
    font-size: 29px;
    letter-spacing: 0.03em;
    white-space: nowrap;
  }
  .person-name {
    position: absolute;
    left: 28px; top: 236px;
    font-size: 29px;
    letter-spacing: 0.04em;
    white-space: nowrap;
  }
  .person-name__first { font-weight: 700; }
  .person-name__last { font-weight: 400; }

  .contact-list {
    position: absolute;
    left: 27px; top: 298px;
    list-style: none;
  }
  .contact-list__item {
    display: flex; align-items: center;
    height: 22.5px;
    font-size: 16px;
    letter-spacing: 0.09em;
    white-space: nowrap;
  }
  .contact-list__item--phone { font-size: 19px; letter-spacing: 0.05em; height: 26px; }
  .contact-list__icon {
    width: 16px; height: 16px;
    margin-right: 11px;
    flex: none;
  }
  .figure-area {
    position: absolute;
    left: 441px; top: 23px;
    width: 236px; height: 356px;
    border-radius: 40px 40px 6px 6px;
    background: linear-gradient(160deg, var(--figure-light) 0%, var(--figure-mid) 45%, var(--figure-deep) 100%);
    opacity: 0.9;
  }
</style>
</head>
<body>
  <section class="card card--front" aria-label="Business card front">
    <div class="front-mark" aria-hidden="true"></div>
    <h1 class="front-name">OAK<br>PARTNERS</h1>
  </section>

  <section class="card card--back" aria-label="Business card back">
    <div class="back-brand">
      <span class="back-brand__mark" aria-hidden="true"></span>
      <span class="back-brand__name">OAK PARTNERS</span>
    </div>

    <p class="person-name"><span class="person-name__first">DORIAN</span> <span class="person-name__last">PEMBERTON</span></p>

    <ul class="contact-list">
      <li class="contact-list__item contact-list__item--phone">
        <svg class="contact-list__icon" viewBox="0 0 16 16" aria-hidden="true">
          <path d="M3 1.5 5.5 4 4.3 6c.9 2 2.6 3.7 4.7 4.7l2-1.2 2.5 2.5-1.8 2.2C7 14 2 9 1 3.3Z" fill="#fff"/>
        </svg>800-555-0147
      </li>
      <li class="contact-list__item">
        <svg class="contact-list__icon" viewBox="0 0 16 16" aria-hidden="true">
          <circle cx="8" cy="8" r="7" fill="none" stroke="#fff" stroke-width="1.4"/>
          <ellipse cx="8" cy="8" rx="3" ry="7" fill="none" stroke="#fff" stroke-width="1.2"/>
          <path d="M1 8h14" stroke="#fff" stroke-width="1.2"/>
        </svg>WWW.OAKPARTNERS.EXAMPLE
      </li>
      <li class="contact-list__item">
        <svg class="contact-list__icon" viewBox="0 0 16 16" aria-hidden="true">
          <rect x="1" y="4" width="14" height="10" fill="none" stroke="#fff" stroke-width="1.3"/>
          <path d="M1 4l7 5 7-5" fill="none" stroke="#fff" stroke-width="1.3"/>
        </svg>DORIAN@OAKPARTNERS.EXAMPLE
      </li>
    </ul>

    <div class="figure-area" role="img" aria-label="Large soft blue brand graphic area"></div>
  </section>
</body>
</html>
```